Design NEW business card

We would like a business card using the colour deep red wine or dark navy blue textured background (patterned or not, open to suggestions) with a high gloss debossed rose gold/copper RM Roland Mercer Jewellery business name (Provided). I have included images for your review we would like to keep our currently logo and business name on the front but you can change the layout and positioning. For the back of the card we are open to all suggestions/variations.
Business
Use our current RM Roland Mercer Jewellery logo (Provided image)

```html
<!DOCTYPE html>
<html lang="en">
<head>
<meta charset="utf-8">
<title>Roland Mercer Jewellery – Business Card</title>
<link rel="stylesheet" href="https://fonts.googleapis.com/css2?family=Montserrat:wght@300;400&display=swap">
<style>
  :root {
    --backdrop: #cdcdcd;
    --wine: #55212a;
    --copper: #b98264;
    --card-white: #f7f7f6;
    --ink: #4a4a4a;
    --muted: #a3a3a3;
  }
  * { margin: 0; padding: 0; box-sizing: border-box; }
  html, body {
    width: 1200px;
    height: 960px;
    overflow: hidden;
    background: var(--backdrop);
    font-family: "Montserrat", sans-serif;
  }
  .canvas { position: relative; width: 1200px; height: 960px; }

  .card { position: absolute; width: 604px; height: 346px; }

  .card-front { left: 320px; top: 108px; background: var(--wine); }
  .brand-lockup {
    position: absolute;
    left: 0; right: 0; top: 188px;
    text-align: center;
    color: var(--copper);
    font-weight: 400;
  }
  .brand-name {
    font-size: 25px;
    letter-spacing: 5px;
    line-height: 1;
  }
  .brand-trade {
    margin-top: 12px;
    font-size: 10px;
    letter-spacing: 11px;
    line-height: 1;
  }

  .card-back { left: 318px; top: 488px; background: var(--card-white); }
  .monogram {
    position: absolute;
    left: 58px; top: 78px;
    color: var(--copper);
    font-size: 58px;
    font-weight: 400;
    letter-spacing: 2px;
    line-height: 1;
  }
  .contact-block { position: absolute; left: 166px; top: 152px; }
  .person-name {
    color: var(--copper);
    font-size: 17px;
    font-weight: 400;
    line-height: 1;
  }
  .person-role {
    margin-top: 8px;
    color: var(--muted);
    font-size: 13px;
    font-weight: 400;
    line-height: 1;
  }
  .address {
    margin-top: 21px;
    color: var(--ink);
    font-size: 14.5px;
    line-height: 17px;
  }
  .contact-list { list-style: none; margin-top: 8px; }
  .contact-list li {
    display: flex;
    align-items: center;
    gap: 8px;
    color: var(--ink);
    font-size: 14.5px;
    line-height: 19.5px;
  }
  .contact-icon { width: 12px; height: 12px; fill: var(--copper); flex: none; }
</style>
</head>
<body>
<main class="canvas">

  <section class="card card-front" aria-label="Card front">
    <div class="brand-lockup">
      <p class="brand-name">ROLAND MERCER</p>
      <p class="brand-trade">JEWELLERY</p>
    </div>
  </section>

  <section class="card card-back" aria-label="Card back">
    <p class="monogram">RM</p>
    <div class="contact-block">
      <p class="person-name">CLARA WHITFIELD</p>
      <p class="person-role">CEO/FOUNDER</p>
      <p class="address">4126 Larkspur Court<br>Fairbanks, Alaska 39812</p>
      <ul class="contact-list">
        <li>
          <svg class="contact-icon" viewBox="0 0 12 12" aria-hidden="true"><path d="M2.4 0.6 L4.3 2.9 L3.2 4.2 C3.9 5.8 5.2 7.1 6.8 7.8 L8.1 6.7 L10.4 8.6 L9.3 10.9 C4.9 10.6 1.4 7.1 1.1 2.7 Z"/></svg>
          512 808 4419
        </li>
        <li>
          <svg class="contact-icon" viewBox="0 0 12 12" aria-hidden="true"><path d="M0.5 2.5 H11.5 V3.4 L6 6.6 L0.5 3.4 Z M0.5 4.6 L6 7.8 L11.5 4.6 V9.8 H0.5 Z"/></svg>
          hello@rmjewels.com
        </li>
        <li>
          <svg class="contact-icon" viewBox="0 0 12 12" aria-hidden="true"><circle cx="6" cy="6" r="5.5"/><path d="M3 4.5 L5 3.5 L6 5 L4.5 6.5 Z M7 7 L9 6.5 L8.5 9 Z" fill="#f7f7f6"/></svg>
          www.rmjewels.com
        </li>
      </ul>
    </div>
  </section>

</main>
</body>
</html>
```